business card for a massage therapy practice named 'Cedar and Willow Massage Studio'

I really need a trendy, yet easy on the eyes business card to complement my logo. Ideally with some gold or rose gold foil work.

My uploaded file of the logo I have in horizontal but I have a vertical version as well. Another color that is used in the website is a blush pink here and there. I'd like to see some trendy tropical leaves in the design.

```html
<!DOCTYPE html>
<html lang="en">
<head>
<meta charset="utf-8">
<title>Cedar and Willow Massage Studio – Business Card</title>
<link href="https://fonts.googleapis.com/css2?family=Heebo:wght@400;500;700&family=Dancing+Script:wght@500&display=swap" rel="stylesheet">
<style>
  :root {
    --backdrop: #e9f1f1;
    --jungle-dark: #0f211b;
    --jungle-deep: #143627;
    --jungle-mid: #2a6a4c;
    --leaf-lime: #7c9a3e;
    --leaf-burgundy: #7a3a44;
    --rose-gold: #e6a6b4;
    --blush: #f4cadb;
    --blush-deep: #eaa9c2;
    --mint: #7fcdb4;
    --gold: #b99b62;
    --ink: #1b1b1b;
    --white: #ffffff;
  }
  * { box-sizing: border-box; margin: 0; padding: 0; }
  html, body { width: 1200px; height: 960px; overflow: hidden; }
  body {
    background: var(--backdrop);
    font-family: 'Heebo', Arial, sans-serif;
    color: var(--ink);
    position: relative;
  }
  .card {
    position: absolute;
    top: 306px;
    width: 400px;
    height: 232px;
    overflow: hidden;
  }

  /* Front */
  .card--front { left: 142px; background: var(--jungle-dark); }
  .front__foliage {
    position: absolute; inset: 0;
    background:
      radial-gradient(ellipse 34% 40% at 50% 50%, var(--jungle-dark) 60%, rgba(15,33,27,0) 100%),
      radial-gradient(circle at 24% 6%, rgba(124,154,62,0.75) 0, rgba(124,154,62,0) 18%),
      radial-gradient(circle at 76% 6%, rgba(124,154,62,0.75) 0, rgba(124,154,62,0) 18%),
      radial-gradient(circle at 30% 96%, rgba(124,154,62,0.6) 0, rgba(124,154,62,0) 16%),
      radial-gradient(circle at 68% 96%, rgba(124,154,62,0.6) 0, rgba(124,154,62,0) 16%),
      radial-gradient(ellipse 14% 22% at 12% 74%, rgba(122,58,68,0.8) 0, rgba(122,58,68,0) 100%),
      radial-gradient(ellipse 14% 22% at 88% 74%, rgba(122,58,68,0.8) 0, rgba(122,58,68,0) 100%),
      radial-gradient(ellipse 12% 16% at 4% 10%, rgba(122,58,68,0.6) 0, rgba(122,58,68,0) 100%),
      radial-gradient(ellipse 12% 16% at 96% 10%, rgba(122,58,68,0.6) 0, rgba(122,58,68,0) 100%),
      radial-gradient(ellipse 70% 75% at 50% 50%, var(--jungle-deep) 45%, var(--jungle-mid) 100%);
  }
  .front__brand {
    position: absolute; left: 0; right: 0; top: 80px;
    display: flex; align-items: center; justify-content: center; gap: 14px;
  }
  .brand-dot {
    width: 30px; height: 30px; border-radius: 50%;
    background: var(--rose-gold);
    flex: none;
  }
  .front__name {
    font-weight: 500; font-size: 26px; line-height: 1.22;
    color: var(--rose-gold); letter-spacing: 0.5px;
  }

  /* Back */
  .card--back { left: 666px; background: var(--white); }
  .back__brand {
    position: absolute; left: 14px; top: 18px;
    display: flex; align-items: center; gap: 7px;
  }
  .back__brand .brand-dot { width: 18px; height: 18px; background: var(--gold); }
  .back__name { font-weight: 500; font-size: 12px; line-height: 1.25; color: var(--ink); }
  .therapist {
    position: absolute; right: 18px; top: 18px; text-align: right;
    font-size: 12px; line-height: 14.5px;
  }
  .therapist__name { font-weight: 700; }
  .sessions__title {
    position: absolute; left: 14px; top: 68px;
    font-family: 'Dancing Script', cursive; font-size: 14px; color: var(--mint);
  }
  .sessions__list {
    position: absolute; left: 17px; top: 90px; width: 370px;
    list-style: none; display: grid; grid-template-columns: 183px 1fr;
    grid-auto-flow: column; grid-template-rows: repeat(3, 13.6px);
    font-size: 10.5px; line-height: 13.6px;
  }
  .sessions__list li { display: flex; align-items: center; gap: 6px; white-space: nowrap; }
  .leaf-bullet { width: 9px; height: 5px; border-radius: 50%; background: var(--blush-deep); transform: rotate(-25deg); flex: none; }
  .contact-band {
    position: absolute; left: 0; right: 0; bottom: 0; height: 89px;
    background: var(--blush);
  }
  .contact-list {
    position: absolute; left: 17px; top: 9px; list-style: none;
    font-size: 11.6px; line-height: 16.8px;
  }
  .contact-list li { display: flex; align-items: center; gap: 8px; white-space: nowrap; }
  .contact-icon { width: 12px; height: 12px; flex: none; }
  .appointment {
    position: absolute; left: 250px; top: 13px; width: 132px; height: 58px;
    background: var(--mint);
  }
  .appointment__label {
    margin: 3px; height: 27px; background: var(--white);
    font-weight: 500; font-size: 11px; line-height: 27px; padding-left: 8px;
  }
  .appointment__phone {
    display: flex; align-items: center; gap: 6px; padding-left: 11px;
    font-weight: 500; font-size: 13px; line-height: 22px;
  }
</style>
</head>
<body>
  <section class="card card--front">
    <div class="front__foliage" role="img" aria-label="Tropical palm leaves, lime lilies and burgundy foliage framing a dark green centre"></div>
    <div class="front__brand">
      <span class="brand-dot"></span>
      <div class="front__name">Cedar &amp; Willow<br>Massage Studio</div>
    </div>
  </section>

  <section class="card card--back">
    <div class="back__brand">
      <span class="brand-dot"></span>
      <div class="back__name">Cedar &amp; Willow<br>Massage Studio</div>
    </div>
    <div class="therapist">
      <div class="therapist__name">Marisol Reyes LMT</div>
      <div>555.204.7381</div>
    </div>
    <div class="sessions__title">Our Most Popular Sessions</div>
    <ul class="sessions__list">
      <li><span class="leaf-bullet"></span>Clinical Bodywork</li>
      <li><span class="leaf-bullet"></span>Therapeutic Massage</li>
      <li><span class="leaf-bullet"></span>Integrated Hot Stone Massage</li>
      <li><span class="leaf-bullet"></span>Lymphatic Drainage Massage</li>
      <li><span class="leaf-bullet"></span>Sacramento Sinus Facial</li>
      <li><span class="leaf-bullet"></span>Australian Foot Treatment</li>
    </ul>
    <div class="contact-band">
      <ul class="contact-list">
        <li>
          <svg class="contact-icon" viewBox="0 0 12 12"><rect x="0.5" y="2" width="11" height="8" fill="#1b1b1b"/><path d="M0.5 2 L6 6.5 L11.5 2" stroke="#f4cadb" stroke-width="1" fill="none"/></svg>
          hello@cedarandwillow.com
        </li>
        <li>
          <svg class="contact-icon" viewBox="0 0 12 12"><rect x="2" y="2.5" width="8" height="5.5" fill="none" stroke="#1b1b1b" stroke-width="1.2"/><rect x="0.5" y="8.8" width="11" height="1.4" fill="#1b1b1b"/></svg>
          www.cedarandwillow.com
        </li>
        <li>
          <svg class="contact-icon" viewBox="0 0 12 12"><circle cx="6" cy="6" r="5" fill="#1b1b1b"/></svg>
          / @cedarandwillow
        </li>
        <li>
          <svg class="contact-icon" viewBox="0 0 12 12"><rect x="1" y="1" width="10" height="10" fill="#1b1b1b"/></svg>
          / @cedarandwillow
        </li>
      </ul>
      <div class="appointment">
        <div class="appointment__label">Call for Appointment</div>
        <div class="appointment__phone">
          <svg class="contact-icon" viewBox="0 0 12 12"><path d="M2.5 1.5 L4.5 1.5 L5 4 L3.8 5 Q4.8 7.2 7 8.2 L8 7 L10.5 7.5 L10.5 9.5 Q10.5 10.5 9.5 10.5 Q1.5 10 1.5 2.5 Q1.5 1.5 2.5 1.5 Z" fill="#1b1b1b"/></svg>
          (555) 204-7381
        </div>
      </div>
    </div>
  </section>
</body>
</html>
```